Book cover - Lanterns Along the Winding Quay

Book cover for Ebook (Quillet) and wrap around print cover (Bindwell) (back, front, and spine)

The book title (may slightly change by end of brief):
(MAIN TITLE) 'Lanterns Along the Winding Quay'
(SUB HEADING) 'A Practical Seasonal Garden Companion for Planting Bulbs, Pruning Hedges and Growing Fresh Herbs'
by Dr Owen Pratchard

I would like a bold, stand out cover. Contemporary. I would like to avoid stereotypical images of people looking anxious or worried. I would like the design to be more uplifting and hopeful, rather than focusing on the negative aspect of anxiety, but avoiding cliched photos of people raising their hands in the air, smiling and jumping etc. The cover should appeal to both men and women.

Trim size of book cover (for BindWell) is 5.25" x 8" back and front with a spine size of 0.477 inches
Updates

Reason: I have decided to extend the deadline by 1 more day, not because I am unhappy with the quality of the designs, but because a few designers have contacted me to explain they have had technical difficulties when submitting their files. Thanks everyone for the hard work and great designs.

Target Market(s)

Males and females (16+) who struggle with social anxiety and shyness

Industry/Entity Type

Social

Font styles to use
Serif

Requirements
Must have
• Bold cover that is modern and contemporary. For example, I like these covers:
• http://lnkvo.test/7kTq3Wm
• http://lnkvo.test/9gHw5Ze
• http://lnkvo.test/4nVy8Kb
• http://lnkvo.test/6jFu2Xo
• http://lnkvo.test/3mEs9Lt
• http://lnkvo.test/8hGz4Nd
• http://lnkvo.test/5bJk7Pv
Nice to have
• Open to abstract designs.
Should not have
• No stereotypical pictures of people who look anxious or worried. Avoid cliched photos of people raising their hands in the air, smiling and jumping etc.

```html
<!DOCTYPE html>
<html lang="en">
<head>
<meta charset="utf-8">
<title>Lanterns Along the Winding Quay — Front Cover</title>
<link rel="stylesheet" href="https://fonts.googleapis.com/css2?family=Bebas+Neue&family=Kaushan+Script&family=Open+Sans:wght@600&family=Questrial&display=swap">
<style>
  :root {
    --stage-bg: #c8c9bb;
    --paper: #ffffff;
    --sea-pale: #d6f1f8;
    --sea-light: #5cc6e8;
    --sea-mid: #1f8fd0;
    --sea-deep: #0b5fae;
    --title-face: #135fae;
    --title-side: #4ea9e4;
    --script-ink: #1b63b2;
    --white-type: #ffffff;
    --shadow: rgba(0, 0, 0, 0.28);
  }
  * { margin: 0; padding: 0; box-sizing: border-box; }
  html, body {
    width: 1200px;
    height: 1000px;
    overflow: hidden;
    background: var(--stage-bg);
  }
  .stage {
    width: 1200px;
    height: 1000px;
    display: flex;
    align-items: center;
    justify-content: center;
  }
  .front-cover {
    position: relative;
    width: 580px;
    height: 950px;
    background: linear-gradient(180deg,
      var(--paper) 0%,
      var(--paper) 40%,
      var(--sea-pale) 52%,
      var(--sea-light) 62%,
      var(--sea-mid) 76%,
      var(--sea-deep) 100%);
    box-shadow: 0 10px 30px var(--shadow);
    display: flex;
    flex-direction: column;
    align-items: center;
    text-align: center;
    overflow: hidden;
  }
  .title {
    display: flex;
    flex-direction: column;
    align-items: center;
    margin-top: 28px;
  }
  .title-script {
    font-family: "Kaushan Script", cursive;
    color: var(--script-ink);
    font-size: 74px;
    line-height: 1;
    font-weight: 400;
  }
  .title-block {
    font-family: "Bebas Neue", sans-serif;
    color: var(--title-face);
    line-height: 0.86;
    letter-spacing: 2px;
    text-shadow: -5px 4px 0 var(--title-side);
  }
  .title-block--along { font-size: 176px; margin-top: 14px; }
  .title-block--winding { font-size: 176px; margin-top: 6px; }
  .title-block--quay {
    font-size: 196px;
    color: var(--white-type);
    text-shadow: -5px 4px 0 var(--sea-mid);
    margin-top: 30px;
  }
  .subtitle {
    font-family: "Open Sans", sans-serif;
    font-weight: 600;
    color: var(--white-type);
    font-size: 18.5px;
    line-height: 1.45;
    margin-top: 26px;
    padding: 0 34px;
  }
  .author {
    font-family: "Questrial", sans-serif;
    color: var(--white-type);
    font-size: 48px;
    letter-spacing: 2px;
    margin-top: auto;
    margin-bottom: 44px;
  }
</style>
</head>
<body>
  <main class="stage">
    <article class="front-cover">
      <h1 class="title">
        <span class="title-script">Lanterns</span>
        <span class="title-block title-block--along">ALONG THE</span>
        <span class="title-block title-block--winding">WINDING</span>
        <span class="title-block title-block--quay">QUAY</span>
      </h1>
      <p class="subtitle">A Practical Seasonal Garden Companion for Planting Bulbs, Pruning Hedges and Growing Fresh Herbs</p>
      <p class="author">DR OWEN PRATCHARD</p>
    </article>
  </main>
</body>
</html>
```